Satchel & Sundial needs new business card design

I need a new business card design. I'm looking for out-of-the-box design which represents the freedom of being a location independent entrepreneur.
I offer coaching, retreats and trips.
I would like to see designs with and without the photo.
Colors I use are black (#000000), green (#25A796) and brown (#D7C38C)
Website satchelandsundial.example

Target Market(s)

location independent entrepreneurs, digital nomads, people looking to swap the 9 to 5 for a lifestyle business

Industry/Entity Type

Business

Contact Information for Business Card

Dorota Falkner
Your Lifestyle Business Coach, Retreat & Trip Leader
http://satchelandsundial.example
hello@satchelandsundial.example
Live a life you don't need a holiday from

Font styles to use
Serif
Sans Serif

Requirements
Must have
• One side should contain only the logo. I would also consider having the "Live a life you don't need a holiday from" on that side too (depending on how it looks)
• Please show both sides on the designs.

```html
<!DOCTYPE html>
<html lang="en">
<head>
<meta charset="utf-8">
<title>Satchel &amp; Sundial — Business Card</title>
<link rel="stylesheet" href="https://fonts.googleapis.com/css2?family=Montserrat:wght@400;500;600;700&display=swap">
<style>
  :root {
    --teal: #25a796;
    --ink: #2b2b2b;
    --grey: #4a4a4a;
    --paper: #ffffff;
    --backdrop: #2a2a2c;
    --sand: #d7c38c;
  }
  * { margin: 0; padding: 0; box-sizing: border-box; }
  html, body {
    width: 1200px;
    height: 950px;
    overflow: hidden;
    background: var(--backdrop);
    font-family: "Montserrat", Arial, sans-serif;
  }
  .sheet {
    width: 1200px;
    height: 950px;
    display: flex;
    flex-direction: column;
    align-items: center;
    justify-content: center;
    gap: 50px;
  }
  .card {
    width: 700px;
    height: 400px;
    position: relative;
    border-radius: 4px;
    box-shadow: 0 10px 30px rgba(0,0,0,0.35);
  }
  /* Front */
  .card--front {
    background: var(--paper);
    display: flex;
    flex-direction: column;
    align-items: center;
    text-align: center;
    padding: 78px 40px 0;
  }
  .wordmark {
    font-weight: 700;
    text-transform: uppercase;
    letter-spacing: 3px;
    line-height: 1;
  }
  .card--front .wordmark {
    font-size: 50px;
    color: var(--ink);
  }
  .holder-name {
    margin-top: 64px;
    font-size: 21px;
    font-weight: 600;
    letter-spacing: 1px;
    text-transform: uppercase;
    color: var(--teal);
  }
  .holder-role {
    margin-top: 8px;
    font-size: 15px;
    color: var(--grey);
  }
  .contact-line {
    margin-top: 14px;
    font-size: 13px;
    color: var(--grey);
  }
  .contact-line .label {
    color: var(--teal);
    font-weight: 700;
  }
  .contact-line .gap { display: inline-block; width: 16px; }
  /* Back */
  .card--back {
    background: var(--teal);
    color: var(--paper);
  }
  .card--back .wordmark {
    position: absolute;
    left: 0;
    right: 0;
    top: 140px;
    text-align: center;
    font-size: 54px;
    color: var(--paper);
  }
  .social-row {
    position: absolute;
    left: 40px;
    bottom: 62px;
    display: flex;
    align-items: center;
    gap: 5px;
  }
  .social-row .chip {
    width: 14px;
    height: 14px;
    background: var(--paper);
    border-radius: 2px;
  }
  .social-row .rule {
    margin-left: 8px;
    width: 560px;
    height: 1px;
    background: var(--paper);
  }
  .tagline {
    position: absolute;
    left: 40px;
    bottom: 36px;
    font-size: 13px;
    font-style: normal;
    letter-spacing: 0.3px;
  }
</style>
</head>
<body>
  <main class="sheet">
    <section class="card card--front" aria-label="Business card front">
      <div class="wordmark">Satchel &amp; Sundial</div>
      <h1 class="holder-name">Dorota Falkner</h1>
      <p class="holder-role">Your Lifestyle Business Coach Retreat &amp; Trip Leader</p>
      <p class="contact-line">
        <span class="label">E :</span> hello@satchelandsundial.example
        <span class="gap"></span>
        <span class="label">W :</span> www.satchelandsundial.example
      </p>
    </section>

    <section class="card card--back" aria-label="Business card back">
      <div class="wordmark">Satchel &amp; Sundial</div>
      <div class="social-row">
        <span class="chip"></span>
        <span class="chip"></span>
        <span class="chip"></span>
        <span class="rule"></span>
      </div>
      <p class="tagline">Live a life you don't need a holiday from</p>
    </section>
  </main>
</body>
</html>
```